Website for new crypto research organization

See brief (attached). This is a pretty basic website with only a handful of pages + ability to collect email addresses.

```html
<!DOCTYPE html>
<html lang="en">
<head>
<meta charset="utf-8">
<title>Tidewater Labs</title>
<link href="https://fonts.googleapis.com/css2?family=Outfit:wght@400;500;600;700&family=Poppins:wght@400;500&display=swap" rel="stylesheet">
<style>
:root{
  --teal:#159a8d;
  --dark:#1e1f21;
  --ink:#1b1b1b;
  --muted:#5d6269;
  --page:#f7f9fb;
  --white:#ffffff;
  --line:#e3e6ea;
}
*{box-sizing:border-box;margin:0;padding:0}
html,body{width:1200px;height:2731px;overflow:hidden}
body{position:relative;background:var(--page);font-family:"Outfit",sans-serif;color:var(--ink)}
.abs{position:absolute}
.center{text-align:center;left:0;width:1200px}

/* header */
.site-header{top:0;left:0;width:1200px;height:105px;background:var(--white)}
.brand{left:111px;top:36px;display:flex;align-items:center;gap:10px;font-size:22px;font-weight:600;color:var(--teal)}
.brand-mark{width:22px;height:22px;border:3px solid var(--teal)}
.main-nav{top:44px;left:0;width:1200px;font-size:16px;color:#2a2a2a}
.main-nav span{position:absolute;transform:translateX(-50%);white-space:nowrap}
.main-nav .active{color:var(--teal)}
.login-icon{display:inline-block;width:9px;height:11px;background:var(--teal);border-radius:5px 5px 2px 2px;margin-right:4px;vertical-align:-1px}

/* hero */
.hero{top:105px;left:0;width:1200px;height:585px;background:var(--dark);overflow:hidden}
.hero-art{left:0;top:0;width:700px;height:585px;background:linear-gradient(135deg,#3d5f8a 0%,#8a6a8f 30%,#b8414a 60%,#d9a13a 85%);-webkit-mask-image:linear-gradient(90deg,#000 55%,transparent 100%);mask-image:linear-gradient(90deg,#000 55%,transparent 100%)}
.hero-title{right:112px;top:190px;font-size:52px;font-weight:700;color:var(--white);letter-spacing:-0.5px}
.hero-text{right:112px;top:265px;text-align:right;white-space:nowrap;font-family:"Poppins",sans-serif;font-size:14.5px;line-height:30px;color:var(--white)}
.btn{display:flex;align-items:center;justify-content:center;background:var(--teal);color:var(--white);font-weight:500;font-size:16px}
.hero-btn{left:870px;top:345px;width:218px;height:57px}
.hero-dots{left:1021px;top:497px;display:flex;gap:4px}
.hero-dots i{width:14px;height:14px;border:2px solid var(--white);border-radius:50%}
.hero-dots i.on{border-color:var(--teal)}

/* section heads */
.sec-title{font-size:46px;font-weight:700}
.sec-text{font-family:"Poppins",sans-serif;font-size:14.5px;line-height:26px;color:var(--muted)}
.rule{left:544px;width:112px;height:4px;background:var(--teal)}

/* research */
.feature{width:310px;text-align:center}
.feature-icon{width:134px;height:134px;border-radius:50%;background:var(--teal);margin:0 auto;display:flex;align-items:center;justify-content:center;box-shadow:0 3px 6px rgba(0,0,0,.15)}
.feature h3{margin-top:14px;font-size:17.5px;font-weight:600}
.feature p{margin-top:10px;font-family:"Poppins",sans-serif;font-size:13.5px;line-height:26px;color:var(--muted)}
.research-btn{left:452px;top:1264px;width:296px;height:58px;box-shadow:0 3px 6px rgba(0,0,0,.18)}

/* news */
.news{top:1398px;left:0;width:1200px;height:640px;background:var(--teal)}
.news .sec-text{color:var(--white)}
.news .rule{background:var(--white)}
.news-card{top:217px;width:317px;height:353px;background:var(--white);border-radius:6px;padding:22px 14px 0 15px}
.news-card h3{font-size:19.5px;font-weight:600}
.news-card time{display:block;margin-top:8px;font-size:14px;color:#333}
.news-card p{margin-top:26px;font-family:"Poppins",sans-serif;font-size:13.5px;line-height:27.5px;color:var(--muted)}
.news-card a{display:inline-block;margin-top:11px;font-size:15px;font-weight:500;color:var(--teal);text-decoration:underline}

/* newsletter */
.email-field{left:218px;top:2300px;width:515px;height:69px;background:var(--white);border-radius:35px;box-shadow:0 2px 6px rgba(0,0,0,.14);padding:0 28px;display:flex;align-items:center;font-family:"Poppins",sans-serif;font-size:14.5px;color:#333}
.subscribe{left:750px;top:2300px;width:231px;height:69px;border-radius:35px;font-size:20px;font-weight:600}

/* footer */
.footer-rule{left:0;top:2456px;width:1200px;height:1px;background:var(--line)}
.footer-nav{top:2538px;left:0;width:1200px;font-size:19px;color:#222}
.footer-nav span{position:absolute;transform:translateX(-50%)}
.social{top:2587px;width:44px;height:44px;border:1px solid #bfc3c8;border-radius:50%}
.copyright{top:2659px;font-size:15px;color:#333}
</style>
</head>
<body>

<header class="abs site-header">
  <div class="abs brand"><span class="brand-mark"></span>Tidewater Labs</div>
  <nav class="abs main-nav">
    <span class="active" style="left:493px">Home</span>
    <span style="left:586px">About Us</span>
    <span style="left:690px">Research</span>
    <span style="left:781px">News</span>
    <span style="left:868px">Careers</span>
    <span style="left:963px">Contact</span>
    <span style="left:1060px"><i class="login-icon"></i>Login</span>
  </nav>
</header>

<section class="abs hero">
  <div class="abs hero-art" role="img" aria-label="Colourful graffiti-painted brick wall photo fading into darkness"></div>
  <h1 class="abs hero-title">Tidewater Labs</h1>
  <p class="abs hero-text">Lorem ipsum dolor sit amet, consectetur adipiscing elit, sed do eiusmod tempor<br>incididunt ut labore et dolore magna aliqua. Ut enim ad minim veniam,</p>
  <div class="abs btn hero-btn">GET STARTED</div>
  <div class="abs hero-dots"><i></i><i></i><i class="on"></i><i></i></div>
</section>

<section class="research">
  <h2 class="abs center sec-title" style="top:757px">Research</h2>
  <p class="abs center sec-text" style="top:823px">Lorem ipsum dolor sit amet, consectetur adipiscing elit, sed do eiusmod tempor<br>incididunt ut labore et dolore magna aliqua.</p>
  <div class="abs rule" style="top:899px"></div>

  <div class="abs feature" style="left:111px;top:954px">
    <div class="feature-icon">
      <svg width="76" height="76" viewBox="0 0 76 76" fill="none" stroke="#fff" stroke-width="3"><circle cx="32" cy="32" r="20"/><line x1="47" y1="47" x2="66" y2="66" stroke-linecap="round"/></svg>
    </div>
    <h3>Lorem ipsum dolor sit amet</h3>
    <p>Lorem ipsum dolor sit amet, adipiscing elit, sed do eiusmod tempor incididunt ut labore et dolore magna aliqua.</p>
  </div>
  <div class="abs feature" style="left:445px;top:954px">
    <div class="feature-icon">
      <svg width="78" height="78" viewBox="0 0 78 78" fill="none" stroke="#fff" stroke-width="3"><rect x="8" y="18" width="60" height="46" rx="4"/><rect x="48" y="34" width="22" height="14" rx="3"/><circle cx="56" cy="41" r="2"/></svg>
    </div>
    <h3>Lorem ipsum dolor sit amet</h3>
    <p>Lorem ipsum dolor sit amet, adipiscing elit, sed do eiusmod tempor incididunt ut labore et dolore magna aliqua.</p>
  </div>
  <div class="abs feature" style="left:780px;top:954px">
    <div class="feature-icon">
      <svg width="78" height="78" viewBox="0 0 78 78" fill="none" stroke="#fff" stroke-width="3"><rect x="8" y="50" width="14" height="18"/><rect x="30" y="36" width="14" height="32"/><rect x="52" y="18" width="14" height="50"/></svg>
    </div>
    <h3>Lorem ipsum dolor sit amet</h3>
    <p>Lorem ipsum dolor sit amet, adipiscing elit, sed do eiusmod tempor incididunt ut labore et dolore magna aliqua.</p>
  </div>

  <div class="abs btn research-btn">RECENT RESEARCH REPORTS</div>
</section>

<section class="abs news">
  <h2 class="abs center sec-title" style="top:55px;color:#fff">Our News</h2>
  <p class="abs center sec-text" style="top:118px">Lorem ipsum dolor sit amet, consectetur adipiscing elit, sed do eiusmod tempor<br>incididunt ut labore et dolore magna aliqua.</p>
  <div class="abs rule" style="top:182px"></div>

  <article class="abs news-card" style="left:111px">
    <h3>Lorem ipsum dolor sit amet,</h3>
    <time>25-01-2022</time>
    <p>Lorem ipsum dolor sit amet, consectetur adipiscing elit, sed do eiusmodincididunt ut labore et dolore magna aliqua. Ut enim ad minim veniam, Lorem ipsum dolor sit amet, consectetur adipiscing elit, sed do eiusmod tempor incididunt</p>
    <a>Read More</a>
  </article>
  <article class="abs news-card" style="left:441px">
    <h3>Lorem ipsum dolor sit amet,</h3>
    <time>25-01-2022</time>
    <p>Lorem ipsum dolor sit amet, consectetur adipiscing elit, sed do eiusmodincididunt ut labore et dolore magna aliqua. Ut enim ad minim veniam, Lorem ipsum dolor sit amet, consectetur adipiscing elit, sed do eiusmod tempor incididunt</p>
    <a>Read More</a>
  </article>
  <article class="abs news-card" style="left:771px">
    <h3>Lorem ipsum dolor sit amet,</h3>
    <time>25-01-2022</time>
    <p>Lorem ipsum dolor sit amet, consectetur adipiscing elit, sed do eiusmodincididunt ut labore et dolore magna aliqua. Ut enim ad minim veniam, Lorem ipsum dolor sit amet, consectetur adipiscing elit, sed do eiusmod tempor incididunt</p>
    <a>Read More</a>
  </article>
</section>

<section class="newsletter">
  <h2 class="abs center sec-title" style="top:2122px">Newsletter</h2>
  <p class="abs center sec-text" style="top:2185px">Lorem ipsum dolor sit amet, consectetur adipiscing elit, sed do eiusmod tempor<br>incididunt ut labore et dolore magna aliqua.</p>
  <div class="abs rule" style="top:2262px"></div>
  <div class="abs email-field">Please enter your email</div>
  <div class="abs btn subscribe">SUBSCRIBE NOW</div>
</section>

<footer>
  <div class="abs footer-rule"></div>
  <nav class="abs footer-nav">
    <span style="left:320px">Home</span>
    <span style="left:430px">About Us</span>
    <span style="left:551px">Research</span>
    <span style="left:656px">News</span>
    <span style="left:758px">Careers</span>
    <span style="left:870px">Contact</span>
  </nav>
  <div class="abs social" style="left:552px" aria-label="Social profile"></div>
  <div class="abs social" style="left:605px" aria-label="Social profile"></div>
  <p class="abs center copyright">© 2022 All Rights Reserved</p>
</footer>

</body>
</html>
```